TK Homes - Stone Dorf Design

Looking for a double sides design, 1 side for my realestate and the other for home building. ( TK Homes on 1 side, Stone Dorf card on the other Side
Side 1 - Marek Tove ~ Vox Realty logo and Company ( the Property quarter )
Marek Tove
Marek@Marektove.example
IG - Marek_Bzq_Realtor
FB - marekt
Cell - 5558130467
3847 61 St Nw

Side 2
Marek Tove
5558130467
IG - Stonedorf_Bzq
Stonedorfdev@mailbox.example

Target Market(s)

Home buyers/ sellers

Industry/Entity Type

Home builders - Realestate

Contact Information for Business Card

Above

Requirements
Must have
• Black OR White background - my information -

```html
<!DOCTYPE html>
<html lang="en">
<head>
<meta charset="utf-8">
<title>Marek Tove – Business Cards</title>
<link rel="stylesheet" href="https://fonts.googleapis.com/css2?family=Tinos:wght@400;700&display=swap">
<style>
  :root {
    --stage: #2b2b30;
    --card: #1e1e22;
    --blue: #0b72c0;
    --yellow: #ffc93c;
    --white: #ffffff;
  }
  * { margin: 0; padding: 0; box-sizing: border-box; }
  html, body { width: 1200px; height: 780px; overflow: hidden; }
  body {
    background: var(--stage);
    font-family: "Tinos", "Times New Roman", serif;
    position: relative;
  }
  .card {
    position: absolute;
    top: 235px;
    width: 540px;
    height: 310px;
    background: var(--card);
    border-radius: 22px;
    border-left: 3px solid var(--yellow);
    border-bottom: 3px solid var(--yellow);
    overflow: hidden;
    box-shadow: 0 18px 40px rgba(0,0,0,.45);
  }
  .card--builder { left: 40px; }
  .card--realty { left: 620px; }

  .brand {
    position: absolute;
    left: 0; top: 0;
    width: 268px; height: 250px;
    display: flex; align-items: center; justify-content: center; gap: 10px;
    color: var(--blue);
    font-weight: 700;
    white-space: nowrap;
  }
  .brand__square { width: 16px; height: 16px; background: var(--yellow); }
  .card--builder .brand__name { font-size: 38px; letter-spacing: 1px; }
  .card--realty .brand__name { font-size: 42px; letter-spacing: 1px; }

  .divider {
    position: absolute;
    left: 268px; top: 50px;
    width: 2px; height: 175px;
    background: var(--white);
  }

  .contact {
    position: absolute;
    left: 292px; top: 46px;
    color: var(--white);
  }
  .card--realty .contact { top: 30px; }
  .contact__name { font-size: 30px; font-weight: 700; line-height: 1; color: var(--blue); }
  .contact__name span { color: var(--yellow); }
  .contact__title { font-size: 15px; font-weight: 700; margin-top: 4px; }
  .contact__address { font-size: 14px; margin-top: 8px; }
  .contact__list { list-style: none; margin-top: 12px; }
  .contact__list li {
    display: flex; align-items: center; gap: 7px;
    font-size: 13.5px; line-height: 20px;
  }
  .icon { width: 12px; height: 12px; flex: none; }
  .icon--dot { border-radius: 50%; background: var(--blue); }
  .card--builder .icon--dot { background: var(--yellow); }

  .band { position: absolute; left: 0; bottom: 0; width: 540px; height: 80px; }
  .band__mark {
    position: absolute;
    left: 268px; bottom: 28px;
    font-size: 10px; font-weight: 700;
    color: var(--blue);
    white-space: nowrap;
  }
</style>
</head>
<body>

<section class="card card--builder" aria-label="Stone Dorf business card">
  <div class="brand">
    <span class="brand__square"></span>
    <span class="brand__name">Stone Dorf</span>
  </div>
  <div class="divider"></div>
  <div class="contact">
    <p class="contact__name">Marek <span>Tove</span></p>
    <p class="contact__title">Director</p>
    <ul class="contact__list">
      <li>
        <svg class="icon" viewBox="0 0 24 24"><path fill="#ffc93c" d="M6.6 10.8a15.1 15.1 0 0 0 6.6 6.6l2.2-2.2c.3-.3.7-.4 1-.2 1.1.4 2.3.6 3.6.6.6 0 1 .4 1 1V20c0 .6-.4 1-1 1A17 17 0 0 1 3 4c0-.6.4-1 1-1h3.5c.6 0 1 .4 1 1 0 1.3.2 2.5.6 3.6.1.3 0 .7-.2 1z"/></svg>
        5558130467
      </li>
      <li><span class="icon icon--dot"></span>Stonedorf_Bzq</li>
      <li>
        <svg class="icon" viewBox="0 0 24 24"><rect x="2" y="5" width="20" height="14" fill="#ffc93c"/><path d="M2 5l10 8 10-8" fill="none" stroke="#1e1e22" stroke-width="2"/></svg>
        Stonedorfdev@mailbox.example
      </li>
    </ul>
  </div>
  <svg class="band" viewBox="0 0 540 80" aria-hidden="true">
    <rect x="0" y="44" width="262" height="18" fill="var(--yellow)"/>
    <polygon points="330,30 540,30 540,46 316,46" fill="var(--blue)"/>
  </svg>
  <span class="band__mark">Stone Dorf</span>
</section>

<section class="card card--realty" aria-label="TK Homes business card">
  <div class="brand">
    <span class="brand__name">TK Homes</span>
  </div>
  <div class="divider"></div>
  <div class="contact">
    <p class="contact__name">Marek <span>Tove</span></p>
    <p class="contact__title">Director</p>
    <p class="contact__address">3847 61 St Nw</p>
    <ul class="contact__list">
      <li>
        <svg class="icon" viewBox="0 0 24 24"><path fill="#0b72c0" d="M6.6 10.8a15.1 15.1 0 0 0 6.6 6.6l2.2-2.2c.3-.3.7-.4 1-.2 1.1.4 2.3.6 3.6.6.6 0 1 .4 1 1V20c0 .6-.4 1-1 1A17 17 0 0 1 3 4c0-.6.4-1 1-1h3.5c.6 0 1 .4 1 1 0 1.3.2 2.5.6 3.6.1.3 0 .7-.2 1z"/></svg>
        5558130467
      </li>
      <li><span class="icon icon--dot"></span>marekt</li>
      <li><span class="icon icon--dot"></span>Marek_Bzq_Realtor</li>
      <li>
        <svg class="icon" viewBox="0 0 24 24"><rect x="2" y="5" width="20" height="14" fill="#0b72c0"/><path d="M2 5l10 8 10-8" fill="none" stroke="#1e1e22" stroke-width="2"/></svg>
        Marek@Marektove.example
      </li>
      <li>
        <svg class="icon" viewBox="0 0 24 24" fill="none" stroke="#0b72c0" stroke-width="2"><circle cx="12" cy="12" r="10"/><path d="M2 12h20M12 2c3 3 3 17 0 20M12 2c-3 3-3 17 0 20"/></svg>
        www.marektove.example
      </li>
    </ul>
  </div>
  <svg class="band" viewBox="0 0 540 80" aria-hidden="true">
    <rect x="0" y="44" width="262" height="18" fill="var(--yellow)"/>
    <polygon points="330,30 540,30 540,46 316,46" fill="var(--blue)"/>
  </svg>
  <span class="band__mark">TK Homes</span>
</section>

</body>
</html>
```